Lumen Harbor is a Smart Device and Wiring Business offering the latest in Smart Home Devices inc

Looking for a new website to draw people to my business and explain what a smart home is all about. I currently own a domain and have a website I put together in webquill business website builder. address www.lumenharbor.example. The website needs modernising and be visually appealing with cool action buttons, client feedback page etc.

The webpage needs to present an image of seamless integration of wireless voice control and smart devices that take tasks and activities away from the owner saving them time and money.

I have a facebook business page(lumen harbor) and instagram linked with the business, are we able to link this to the website somehow?

Target Market(s)

Residential home owners who want to modernise their home. Who have seen adverts for corvo hub and pellar mira and want to put it in their home.

Industry/Entity Type

Technology Equipment

Number of Pages Required

1 page

Colors

Designer to choose colors to be used in the design.

Requirements
Must have
• A great landing page, that is modern and attractive, that gets across the idea of smart devices and technology.
• Must be ios/android device friendly.
Nice to have
• interactive/animated buttons
• I like the direction and interactiveness of these websites, a simplified version would be awesome.
• Something in between:
• http://www.quorbeliving.example/ and https://plindo.example/
• http://www.quorbeliving.example/

```html
<!DOCTYPE html>
<html lang="en">
<head>
<meta charset="utf-8">
<title>Lumen Harbor — Smart Home Integration</title>
<link rel="stylesheet" href="https://fonts.googleapis.com/css2?family=Open+Sans:ital,wght@0,400;0,600;0,700;0,800;1,400&family=Dancing+Script:wght@600&display=swap">
<style>
:root{
  --blue:#1e8fd0;
  --blue-btn:#2a8fd3;
  --green:#8db43b;
  --sky-top:#a9d9f1;
  --sky-low:#e3f3fb;
  --text:#555b60;
  --text-dark:#2f3336;
  --white:#ffffff;
  --footer:#3b3b3b;
  --footer-line:#555555;
  --field:rgba(255,255,255,.55);
}
*{box-sizing:border-box;margin:0;padding:0}
html,body{width:1200px;height:4018px;overflow:hidden}
body{font-family:"Open Sans",Arial,sans-serif;color:var(--text);background:var(--white);position:relative}
section,header,footer{position:absolute;left:0;width:1200px}
.abs{position:absolute}
.section-title{position:absolute;left:0;width:1200px;text-align:center;font-size:33px;font-weight:700;letter-spacing:1px;color:var(--blue)}
.btn{position:absolute;height:34px;line-height:34px;border-radius:4px;background:var(--blue-btn);color:var(--white);font-size:12px;font-weight:700;text-align:center;letter-spacing:.5px;text-transform:uppercase;box-shadow:0 2px 0 rgba(0,0,0,.12)}

/* hero */
.hero{top:0;height:482px;background:linear-gradient(180deg,var(--sky-top),var(--sky-low))}
.logo{position:absolute;left:104px;top:14px;display:flex;align-items:center;gap:10px}
.logo-dot{width:44px;height:44px;border-radius:50%;background:var(--blue)}
.logo-name{font-size:24px;font-weight:700;color:var(--blue);letter-spacing:.5px}
.nav{position:absolute;top:30px;left:0;width:1200px;font-size:13px;font-weight:700;color:var(--blue)}
.nav span{position:absolute}
.hero-art{left:84px;top:118px;width:420px;height:434px;border-radius:14px;background:linear-gradient(180deg,rgba(255,255,255,.55) 0%,#e4f3fb 35%,#f1e3d6 62%,#7d9fb4 85%,#4c5a63 100%);z-index:2}
.hero-title{left:614px;top:172px;font-size:32px;font-weight:700;color:var(--blue)}
.hero-sub{left:614px;top:222px;width:520px;font-size:13px;font-weight:600;color:#5d6a73;line-height:20px}
.hero-note{left:614px;top:294px;font-size:13px;color:#5d6a73}

/* about */
.about{top:477px;height:541px;background:var(--green)}
.about .section-title{top:125px;color:var(--white)}
.about p{position:absolute;left:292px;width:616px;text-align:center;color:var(--white);font-size:13px;font-weight:600;line-height:20px}

/* what we do */
.what{top:1018px;height:643px;background:var(--white)}
.what p{position:absolute;left:228px;width:744px;text-align:center;font-size:13px;line-height:20px;color:var(--text)}
.step{position:absolute;width:200px;text-align:center}
.step-photo{width:156px;height:156px;border-radius:50%;margin:0 auto;border:4px solid #fff;box-shadow:0 4px 10px rgba(0,0,0,.25)}
.step-num{position:absolute;left:76px;top:506px;width:48px;height:48px;border-radius:50%;background:var(--blue);color:#fff;font-weight:700;font-size:16px;line-height:48px;text-align:center}
.step-label{position:absolute;top:568px;left:0;width:200px;font-size:14px;font-weight:700;color:var(--blue);letter-spacing:.5px}

/* specialists */
.specialists{top:1661px;height:568px;background:linear-gradient(180deg,#e9ebec,#d6d9db 60%,#c9cdd0)}
.specialists .section-title{top:55px}
.spec-phone{left:263px;top:121px;width:308px;height:383px;background:linear-gradient(135deg,#9a7d64,#5e8fc4 55%,#3c4a5b)}
.spec-card{left:571px;top:142px;width:367px;height:346px;background:#fff;box-shadow:0 3px 12px rgba(0,0,0,.2)}
.spec-card h3{position:absolute;top:24px;width:367px;text-align:center;font-size:20px;font-weight:600;color:#6d7378}
.spec-card p{position:absolute;left:70px;top:62px;width:227px;text-align:center;font-size:13px;line-height:19px;color:#7a7f83}
.feature{position:absolute;width:96px;text-align:center;top:226px;font-size:12px;line-height:16px;color:var(--text-dark)}
.feature i{display:block;width:58px;height:58px;border-radius:50%;margin:0 auto 8px;background:linear-gradient(135deg,#444,#111)}
.card-arrow{position:absolute;top:240px;color:var(--blue);font-size:20px}
.spec-art{left:938px;top:161px;width:262px;height:376px;background:linear-gradient(135deg,#cfe8a8,#f3c34a 45%,#6ab034 80%,#2a2a2a)}

/* testimonial */
.testimonial{top:2229px;height:370px;background:#fff}
.testimonial .section-title{top:55px}
.client-photo{left:144px;top:130px;width:184px;height:184px;border-radius:50%;background:linear-gradient(180deg,#dfe6ec,#8fa3b8);box-shadow:0 3px 10px rgba(0,0,0,.2)}
.quote{left:356px;top:190px;width:680px;font-style:italic;font-size:13px;line-height:20px;color:#7b8085}
.quote-line{left:356px;top:255px;width:52px;height:3px;background:var(--blue)}
.quote-name{left:418px;top:238px;font-family:"Dancing Script",cursive;font-size:24px;color:var(--text-dark)}
.slide-arrow{top:200px;font-size:28px;color:#b9bdc0}

/* blog */
.blog{top:2599px;height:482px;background:var(--green)}
.blog .section-title{top:55px;color:#fff}
.post{position:absolute;top:126px;width:500px;height:225px;background:#fff;box-shadow:0 2px 6px rgba(0,0,0,.15)}
.post-img{position:absolute;left:0;top:0;width:178px;height:225px}
.post-date{position:absolute;left:215px;top:38px;font-size:13px;color:#444}
.post-title{position:absolute;left:215px;top:62px;font-size:14px;font-weight:700;color:#222}
.post-text{position:absolute;left:215px;top:94px;width:265px;font-size:12.5px;font-style:italic;line-height:18px;color:#444}

/* contact */
.contact{top:3081px;height:608px;background:linear-gradient(180deg,#f4f4f4,#e4e4e2 50%,#d9d9d5)}
.contact .section-title{top:55px}
.field{position:absolute;left:263px;width:675px;border:1px solid #c9c9c9;background:var(--field);font-size:12px;font-weight:700;color:#333;padding:10px 12px;letter-spacing:.3px}
.checkbox{position:absolute;left:263px;top:252px;font-size:11px;color:#555;display:flex;align-items:center;gap:6px}
.checkbox i{width:10px;height:10px;border:1px solid #888;background:#fff;display:block}

/* footer */
.footer{top:3689px;height:329px;background:var(--footer);color:#fff}
.footer h4{position:absolute;top:38px;font-size:14px;font-weight:700;letter-spacing:.5px}
.quick-links{position:absolute;left:86px;top:70px;list-style:none;font-size:12px;font-weight:700}
.quick-links li{height:42.5px}
.quick-links li::before{content:"›";margin-right:10px}
.news-input{position:absolute;left:351px;top:88px;width:271px;height:41px;border:1px solid var(--footer-line);font-size:12px;color:#aaa;line-height:39px;padding-left:42px}
.news-input svg{position:absolute;left:14px;top:13px}
.subscribe{left:630px;top:88px;width:131px;height:41px;line-height:41px;border-radius:0}
.social{position:absolute;top:169px;width:42px;height:42px;border-radius:50%}
.footer-map{left:876px;top:43px;width:236px;height:214px;background:linear-gradient(135deg,#eef0e8,#dfe3d6)}
.copyright{position:absolute;left:0;top:282px;width:1200px;text-align:center;font-size:11px;color:#999;letter-spacing:.5px}
</style>
</head>
<body>

<header class="hero">
  <div class="logo"><span class="logo-dot"></span><span class="logo-name">Lumen Harbor</span></div>
  <nav class="nav">
    <span style="left:609px">HOME</span>
    <span style="left:686px">WHAT WE DO</span>
    <span style="left:815px">PRODUCTS</span>
    <span style="left:925px">ABOUT US</span>
    <span style="left:1031px">CONTACT US</span>
  </nav>
  <div class="abs hero-art" role="img" aria-label="Illustration of a connected house with smart device icons floating above it, a tablet showing a thermostat reading and a red car"></div>
  <h1 class="abs hero-title">SMART DEVICE INTEGRATION</h1>
  <p class="abs hero-sub">We are focused on delivering affordable and easily usable devices for home and office</p>
  <p class="abs hero-note">Wireless smart home - No need for Pre - wired cabling</p>
  <span class="btn" style="left:614px;top:336px;width:150px">Read More</span>
</header>

<section class="about">
  <h2 class="section-title">ABOUT US</h2>
  <p style="top:206px">Lorem Ipsum is simply dummy text of the printing and typesetting industry. Lorem Ipsum has been the industry's standard dummy text ever since the 1500s, when an unknown printer took a galley of type and scrambled it to make a type specimen book. It has survived not only five centuries.</p>
  <p style="top:318px">Lorem Ipsum is simply dummy text of the printing and typesetting industry. Lorem Ipsum has been the industry's standard dummy text ever since the 1500s, when an unknown printer took a galley of type and scrambled it to make a type specimen book. It has survived not only five centuries.</p>
  <span class="btn" style="left:525px;top:446px;width:150px">Read More</span>
</section>

<section class="what">
  <h2 class="section-title" style="top:55px">WHAT WE DO</h2>
  <p style="top:140px">We are a small group of Calloway Tech consultants, with long-term experience in the integration, setup and fault finding of advanced technologies, we are passionate about the products we sell and confident in the service we provide.</p>
  <p style="top:200px">Our aim is to simplify the mystery and confusion surrounding Smart Devices and Internet of Things (IOT) products and incorporate them into your lives, making them easier and more time rich.</p>
  <svg class="abs" style="left:0;top:500px" width="1200" height="60" viewBox="0 0 1200 60" aria-hidden="true">
    <path d="M228 30 C300 0 320 60 398 30 M498 30 C570 60 600 0 661 30 M761 30 C840 0 870 60 973 30" fill="none" stroke="#6aa9d6" stroke-width="2" stroke-dasharray="6 5"/>
  </svg>
  <div class="step" style="left:104px;top:312px">
    <div class="step-photo" role="img" aria-label="Photo of consultants meeting with a client" style="background:linear-gradient(135deg,#e9d7c4,#6f8fb0)"></div>
  </div>
  <div class="step" style="left:374px;top:312px">
    <div class="step-photo" role="img" aria-label="Photo of a smart home control interface" style="background:linear-gradient(135deg,#cfe3ea,#5a8a9a)"></div>
  </div>
  <div class="step" style="left:637px;top:312px">
    <div class="step-photo" role="img" aria-label="Photo of a wall mounted smart thermostat" style="background:linear-gradient(135deg,#9aa4ad,#3d4650)"></div>
  </div>
  <div class="step" style="left:897px;top:312px">
    <div class="step-photo" role="img" aria-label="Photo of two hands joined in support" style="background:linear-gradient(135deg,#f4ece6,#c9b4a6)"></div>
  </div>
  <div class="step" style="left:104px;top:0;height:600px"><span class="step-num">1</span><span class="step-label">CONSULTATION</span></div>
  <div class="step" style="left:374px;top:0;height:600px"><span class="step-num">2</span><span class="step-label">INSTALLATION</span></div>
  <div class="step" style="left:637px;top:0;height:600px"><span class="step-num">3</span><span class="step-label">FINALISATION</span></div>
  <div class="step" style="left:897px;top:0;height:600px"><span class="step-num">4</span><span class="step-label">SUPPORT</span></div>
</section>

<section class="specialists" aria-label="Smart home specialists">
  <div class="abs" role="img" aria-label="Faded photo of a bright modern living room" style="left:0;top:0;width:1200px;height:568px;background:linear-gradient(90deg,rgba(255,255,255,.35),rgba(255,255,255,0) 40%,rgba(255,255,255,.3))"></div>
  <h2 class="section-title">SMART HOME SPECIALISTS</h2>
  <div class="abs spec-phone" role="img" aria-label="Photo of a hand holding a phone with a home automation app"></div>
  <div class="abs spec-card">
    <h3>Home Automation</h3>
    <p>Show us your Vision and we'll create reality, by bringing technology and your home or office together.</p>
    <span class="btn" style="left:107px;top:162px;width:150px;height:34px">Read More</span>
    <span class="card-arrow" style="left:12px">‹</span>
    <span class="card-arrow" style="left:346px">›</span>
    <div class="feature" style="left:30px"><i role="img" aria-label="Voice speaker photo"></i>Voice Control With pellar mira</div>
    <div class="feature" style="left:136px"><i role="img" aria-label="Smart lock photo" style="background:linear-gradient(135deg,#8a1f1f,#1a1a1a)"></i>Keyless Entry</div>
    <div class="feature" style="left:242px"><i role="img" aria-label="Home theatre photo" style="background:linear-gradient(135deg,#6f6f6f,#1c1c1c)"></i>Home Theatre Design</div>
  </div>
  <div class="abs spec-art" role="img" aria-label="Illustration of a phone and light bulb linked to green smart device icons"></div>
</section>

<section class="testimonial">
  <h2 class="section-title">TESTIMONIAL</h2>
  <span class="abs slide-arrow" style="left:92px">‹</span>
  <div class="abs client-photo" role="img" aria-label="Portrait photo of the client"></div>
  <p class="abs quote">"Lorem ipsum dolor sit amet, consectetur adipiscing elit, sed do eiusmod tempor incididunt ut labore et dolore magna aliqua. Ut enim ad minim veniam, quis nostrud exercitation."</p>
  <span class="abs quote-line"></span>
  <span class="abs quote-name">John Doe</span>
  <span class="abs slide-arrow" style="left:1090px">›</span>
</section>

<section class="blog">
  <h2 class="section-title">BLOG</h2>
  <article class="post" style="left:86px">
    <div class="post-img" role="img" aria-label="Photo of a modern living room" style="background:linear-gradient(135deg,#d9d2c8,#8b8176)"></div>
    <span class="post-date">February 22, 2016</span>
    <h3 class="post-title">LOREM IPSUM DOLOR</h3>
    <p class="post-text">Lorem ipsum dolor sit amet, consectetur adipiscing elit, sed do eiusmod tempor incididunt ut labore et dolore magna aliqua. Ut enim ad minim exercitation.</p>
  </article>
  <article class="post" style="left:614px">
    <div class="post-img" role="img" aria-label="Photo of a hand using a smart home app on a phone" style="background:linear-gradient(135deg,#f0c7a8,#4d9fd6)"></div>
    <span class="post-date">February 22, 2016</span>
    <h3 class="post-title">LOREM IPSUM DOLOR</h3>
    <p class="post-text">Lorem ipsum dolor sit amet, consectetur adipiscing elit, sed do eiusmod tempor incididunt ut labore et dolore magna aliqua. Ut enim ad minim exercitation.</p>
  </article>
  <span class="btn" style="left:525px;top:386px;width:150px">View More</span>
</section>

<section class="contact">
  <div class="abs" role="img" aria-label="Faded photo of a white modern lounge" style="left:0;top:0;width:1200px;height:608px;background:linear-gradient(90deg,rgba(255,255,255,.4),rgba(255,255,255,0) 50%,rgba(255,255,255,.4))"></div>
  <h2 class="section-title">CONTACT US</h2>
  <div class="field" style="top:142px;height:40px">NAME</div>
  <div class="field" style="top:195px;height:41px">EMAIL</div>
  <div class="checkbox"><i></i>Check Here To Receive Mail Updates</div>
  <div class="field" style="top:281px;height:35px;padding-top:7px">SUBJECT</div>
  <div class="field" style="top:335px;height:147px">MESSAGE</div>
  <span class="btn" style="left:525px;top:511px;width:150px">Send</span>
</section>

<footer class="footer">
  <h4 style="left:86px">QUICK LINK</h4>
  <ul class="quick-links">
    <li>HOME</li><li>WHAT WE DO</li><li>PRODUCTS</li><li>ABOUT US</li><li>CONTACT US</li>
  </ul>
  <h4 style="left:351px">NEWS LETTER</h4>
  <div class="news-input">
    <svg width="16" height="12" viewBox="0 0 16 12" aria-hidden="true"><rect x="0.5" y="0.5" width="15" height="11" fill="none" stroke="#aaa"/><path d="M1 1l7 6 7-6" fill="none" stroke="#aaa"/></svg>
    Email Address
  </div>
  <span class="btn subscribe">Subscribe</span>
  <span class="social" style="left:351px;background:#3b5a9a" aria-label="Social profile link 1"></span>
  <span class="social" style="left:402px;background:#33a7dd" aria-label="Social profile link 2"></span>
  <span class="social" style="left:453px;background:#d84a38" aria-label="Social profile link 3"></span>
  <span class="social" style="left:507px;background:#3f6ea2" aria-label="Social profile link 4"></span>
  <div class="abs footer-map" role="img" aria-label="Street map showing the business location"></div>
  <p class="copyright">2016 © LUMEN HARBOR. ALL RIGHTS RESERVED</p>
</footer>

</body>
</html>
```